Book Cover for a Short Story called “Leaving Harbor"

Pretty Straightforward. Looking for a 5.5X8.5 book cover. The story is a very short (40 pages) story about a man who moves from Greece to Canada in 1920. I have three photos to provide. One is the house that he left in greece. THen I have photos of him and his wife who he met in Toronto. I think I want the house photo on the front...
I will need cover for paper back and e-book. The ISBN numbers are:

ISBN: 978-1-5523094-2-7 (e-book)
ISBN: 978-1-5523094-1-0 (paperback)

If you want you can read it at https://kevinmarlow.example/fiction/leaving-harbor/

Colors
0094D4
00A9DD
6FCCEA
C7EBF8
E9F6FB

Requirements
Must have
• Room for a blurb about the book on the back cover. ISBN Number

```html
<!DOCTYPE html>
<html lang="en">
<head>
<meta charset="utf-8">
<title>Leaving Harbor – Cover Spread</title>
<link rel="stylesheet" href="https://fonts.googleapis.com/css2?family=EB+Garamond:wght@400;500&family=Open+Sans:wght@400;700&display=swap">
<style>
  :root {
    --stage: #4b4b4b;
    --paper: #ffffff;
    --ink: #2e2a22;
    --body-ink: #3a3a3a;
    --isbn-ink: #111111;
    --sepia-light: #d8c9ab;
    --sepia-mid: #cdbd9d;
    --sepia-deep: #8f8470;
    --photo-dark: #6e665a;
    --portrait-tone: #a7adba;
  }
  * { margin: 0; padding: 0; box-sizing: border-box; }
  html, body {
    width: 1200px; height: 761px; overflow: hidden;
    background: var(--stage);
  }
  .spread {
    position: absolute; left: 133px; top: 20px;
    width: 934px; height: 720px;
    display: flex; background: var(--paper);
  }
  /* Back cover */
  .back-cover {
    position: relative; width: 471px; height: 100%;
    background: var(--paper);
  }
  .back-title {
    position: absolute; left: 0; width: 100%; top: 88px;
    text-align: center;
    font-family: "EB Garamond", Georgia, serif;
    font-size: 46px; font-weight: 400; color: var(--ink);
    letter-spacing: 0.5px;
  }
  .blurb {
    font-family: "Open Sans", Arial, sans-serif;
    font-size: 9.6px; line-height: 15px; color: var(--body-ink);
    text-align: justify;
  }
  .blurb-intro {
    position: absolute; left: 48px; top: 157px; width: 379px;
  }
  .author-bio {
    position: absolute; left: 224px; top: 270px; width: 203px;
  }
  .author-bio p + p { margin-top: 15px; }
  .author-portrait {
    position: absolute; left: 10px; top: 252px;
    width: 206px; height: 312px;
    background: linear-gradient(180deg, var(--portrait-tone) 0%, var(--portrait-tone) 60%, rgba(255,255,255,0) 100%);
  }
  .isbn {
    position: absolute; left: 33px; top: 659px;
    font-family: "Open Sans", Arial, sans-serif;
    font-size: 9.8px; font-weight: 700; color: var(--isbn-ink);
  }
  /* Front cover */
  .front-cover {
    position: relative; width: 463px; height: 100%;
    background: linear-gradient(180deg, var(--sepia-mid) 0%, var(--sepia-light) 30%, var(--sepia-light) 100%);
    overflow: hidden;
  }
  .house-photo {
    position: absolute; left: 0; top: 320px; width: 100%; height: 270px;
    background: linear-gradient(180deg, rgba(216,201,171,0) 0%, var(--sepia-deep) 35%, var(--photo-dark) 80%, var(--sepia-deep) 100%);
  }
  .torn-edge { position: absolute; left: 0; top: 556px; width: 463px; height: 164px; }
  .front-title {
    position: absolute; left: 0; width: 100%; top: 52px;
    text-align: center;
    font-family: "EB Garamond", Georgia, serif;
    font-weight: 400; color: var(--ink);
    font-size: 118px; line-height: 130px;
  }
  .front-author {
    position: absolute; left: 0; width: 100%; top: 628px;
    text-align: center;
    font-family: "EB Garamond", Georgia, serif;
    font-size: 38px; font-weight: 500; letter-spacing: 6px;
    color: var(--ink);
  }
</style>
</head>
<body>
  <main class="spread">
    <section class="back-cover">
      <h2 class="back-title">Leaving Harbor</h2>
      <p class="blurb blurb-intro">Lorem ipsum dolor sit amet, consectetur adipiscing elit, sed do eiusmod tempor incididunt ut labore et dolore magna aliqua. Quis ipsum suspendisse ultrices gravida. Risus commodo viverra maecenas accumsan lacus vel facilisis. Lorem ipsum dolor sit amet, consectetur adipiscing elit, sed do eiusmod tempor incididunt ut labore et dolore magna aliqua.</p>
      <div class="author-portrait" role="img" aria-label="Author portrait photograph, fading to white at the bottom"></div>
      <div class="blurb author-bio">
        <p>Quis ipsum suspendisse ultrices gravida. Risus commodo viverra maecenas accumsan lacus vel facilisis. Lorem ipsum dolor sit amet, consectetur adipiscing elit, sed do eiusmod tempor incididunt ut labore et dolore magna aliqua. Quis ipsum suspendisse ultrices gravida. Risus commodo viverra maecenas accumsan lacus vel facilisis.</p>
        <p>Quis ipsum suspendisse ultrices gravida. Risus commodo viverra maecenas accumsan lacus vel facilisis. Lorem ipsum dolor sit amet, consectetur adipiscing elit, sed do eiusmod tempor incididunt ut labore et dolore magna aliqua. Quis ipsum suspendisse ultrices gravida. Risus commodo viverra maecenas accumsan lacus vel facilisis.</p>
      </div>
      <p class="isbn">ISBN: 978-1-5523094-1-0</p>
    </section>
    <section class="front-cover">
      <div class="house-photo" role="img" aria-label="Sepia photograph of an old stone house in a Greek village with a tiled roof and a pile of rocks in front"></div>
      <svg class="torn-edge" viewBox="0 0 463 164" preserveAspectRatio="none" aria-hidden="true">
        <path d="M0 30 L18 24 L34 28 L52 20 L70 26 L88 18 L104 22 L122 16 L140 24 L158 18 L176 26 L196 20 L214 28 L232 22 L252 30 L270 22 L288 26 L306 18 L326 24 L344 16 L362 22 L380 14 L398 20 L416 12 L434 18 L450 10 L463 14 L463 164 L0 164 Z" fill="#ffffff"/>
      </svg>
      <h1 class="front-title">Leaving<br>Harbor</h1>
      <p class="front-author">KEVIN MARLOW</p>
    </section>
  </main>
</body>
</html>
```